tinyTally Resource Book - 10 maths tasks to do outside

I need a 22 (11 pages back to back) page A6 sized book produced to standard for submission to professional printer. Needs to be as .pdf file showing guide lines and allowances for colour bleed. I have text already written and submitted as attachment in a Word file with margins set to A6 size. The theme of the materials is "Nature Play" so using lots of pictures from nature (Australia preferably) and showing lots of patterns in nature (rocks, leaves, flower petals etc). Some of the tasks refer to specific activities, such as "shadows" and "floating" so would be great to illustrate appropriately. The big emphasis is on learning outside the classroom, getting kids to engage actively with nature. I would like to see the pages as full colour - so not white background. The book itself will be spiral bound along the top edge so a margin of at least 1cm will be required at the top of each page (or the bottom of even numbered pages). Book will be printed on plastic laminated matte paper for outdoor use. Font size needs to be big enough to read. Fonts sizes, alignments and page numbers are all different at the moment and need to be standardised. One photo is included in a page as a sample if you can use it, otherwise disregard. Logo for Wattlebrook Numeracy Guild is also included to have as part of the acknowledgements at the back of the book.

Target Market(s)

Book is for early childhood and preschool teachers.

Industry/Entity Type

Education

Font styles to use
Sans Serif

Requirements
Must have
• Colour and appeal.
Nice to have
• Use of natural colours instead of bright catchy colours but that is your call.
Should not have
• American spelling

```html
<!DOCTYPE html>
<html lang="en-AU">
<head>
<meta charset="utf-8">
<title>10. Repeat My Pattern</title>
<link rel="stylesheet" href="https://fonts.googleapis.com/css2?family=Jost:ital,wght@0,400;0,700;0,800;1,700&display=swap">
<style>
  :root {
    --paper: #ffffff;
    --navy: #1f2d7b;
    --ink: #2a2a2a;
    --diamond: #d7262e;
    --leaf-red: #f2a79c;
    --leaf-peach: #f8cfb8;
    --leaf-gold: #f6dfa2;
    --crop: #555555;
  }
  html, body {
    margin: 0;
    padding: 0;
    width: 889px;
    height: 1200px;
    overflow: hidden;
    background: var(--paper);
  }
  .sheet {
    position: relative;
    width: 889px;
    height: 1200px;
    font-family: "Jost", "Futura", sans-serif;
  }
  .crop-marks { position: absolute; inset: 0; }
  .page {
    position: absolute;
    left: 52px;
    top: 52px;
    width: 784px;
    height: 1096px;
    overflow: hidden;
  }
  .page__backdrop {
    position: absolute;
    inset: 0;
    background:
      radial-gradient(ellipse at 20% 15%, var(--leaf-gold) 0%, transparent 40%),
      radial-gradient(ellipse at 80% 70%, var(--leaf-red) 0%, transparent 45%),
      radial-gradient(ellipse at 15% 75%, var(--leaf-red) 0%, transparent 40%),
      linear-gradient(160deg, var(--leaf-peach) 0%, #fbe9e2 50%, var(--leaf-peach) 100%);
  }
  .page__content { position: absolute; inset: 0; color: var(--navy); }
  .halo { text-shadow: 0 0 3px #fff, 0 0 6px #fff; }
  .task-title {
    position: absolute;
    left: 0; right: 0; top: 50px;
    margin: 0;
    text-align: center;
    font-weight: 800;
    font-size: 47px;
    line-height: 60px;
  }
  .outcome {
    position: absolute;
    left: 20px; right: 20px; top: 126px;
    margin: 0;
    text-align: center;
    font-weight: 700;
    font-size: 32px;
    line-height: 44px;
  }
  .lead {
    position: absolute;
    left: 72px;
    margin: 0;
    white-space: nowrap;
    font-style: italic;
    font-weight: 700;
    font-size: 28px;
    line-height: 36px;
  }
  .body {
    position: absolute;
    left: 144px;
    margin: 0;
    white-space: nowrap;
    color: var(--ink);
    font-weight: 400;
    font-size: 35px;
    line-height: 45px;
  }
  .lead--children { top: 232px; }
  .body--recognise { top: 308px; }
  .lead--educators { top: 440px; }
  .body--provide { top: 480px; }
  .lead--task { top: 703px; }
  .aims {
    position: absolute;
    left: 144px; top: 740px;
    margin: 0; padding: 0;
    list-style: none;
    white-space: nowrap;
    color: var(--ink);
    font-size: 30px;
    letter-spacing: 0.4px;
    line-height: 36px;
  }
  .aims li { position: relative; padding-left: 20px; }
  .aims li::before {
    content: "";
    position: absolute;
    left: -4px; top: 11px;
    width: 14px; height: 14px;
    background: var(--diamond);
    transform: rotate(45deg);
  }
  .leaf-row {
    position: absolute;
    left: 448px; top: 896px;
    width: 308px; height: 80px;
    border-radius: 8px;
    background: linear-gradient(90deg, #e0a243 0%, #d9732f 30%, #8ea33a 62%, #d98a36 100%);
  }
</style>
</head>
<body>
<div class="sheet">
  <svg class="crop-marks" width="889" height="1200" viewBox="0 0 889 1200" aria-hidden="true">
    <g stroke="var(--crop)" stroke-width="1" fill="none">
      <path d="M52 0V36M0 52H36M74 36V74M36 74H74"/>
      <path d="M837 0V36M889 52H853M815 36V74M853 74H815"/>
      <path d="M52 1200V1164M0 1148H36M74 1164V1126M36 1126H74"/>
      <path d="M837 1200V1164M889 1148H853M815 1164V1126M853 1126H815"/>
    </g>
  </svg>

  <section class="page">
    <div class="page__backdrop" role="img" aria-label="Background photograph of scattered red and golden autumn leaves"></div>
    <div class="page__content">
      <h1 class="task-title halo">10. Repeat My Pattern</h1>
      <h2 class="outcome halo">NPLF – Outcome 5: Children are keen<br>communicators</h2>

      <p class="lead lead--children halo">Children begin to understand how symbols and<br>pattern systems work when they...</p>
      <p class="body body--recognise">begin to recognise patterns and<br>relationships and the connections<br>between them</p>

      <p class="lead lead--educators halo">Educators promote this learning when they...</p>
      <p class="body body--provide">provide children with access to a<br>wide range of everyday materials<br>that they can use to create patterns<br>and to sort, categorise, order and<br>compare</p>

      <p class="lead lead--task halo">This task provides an opportunity to:</p>
      <ul class="aims">
        <li>explore the concepts of “pattern” and<br>“repeat”</li>
        <li>create, repeat and describe patterns</li>
        <li>explore connections between patterns<br>and relationships</li>
        <li>develop awareness<br>of regular cycles</li>
      </ul>

      <div class="leaf-row" role="img" aria-label="Row of four maple leaves in a repeating colour pattern: gold, orange, green, orange"></div>
    </div>
  </section>
</div>
</body>
</html>
```